Design and Renovation Company Luxury Business Card

I want to create a luxury business card for a Design and Renovation Firm . We will use our current logo. The company name is 528BUILDA. We do not want anything standard. We need a very unique concept.
Please see uploaded inspiration. I really like the textured paper option. I would like the card to be thick with debossing, and/or embossing options. The logo has orange in it but I would like to see the card with and without the orange. I think the orange may make the company feel less high-end. The goal is to elevate the logo not match its vibe per se of the logo. We want something very unique, not standard at all!
I would like a space for :
Logo,
Name,
Position,
Email,
Office number,
Website Address,
Business Address,
Thank you!
Have fun!
Target Market(s)
Home owners Age 35 +
Industry/Entity Type
Design and Renovation
Contact Information for Business Card
Logo, Name, Position, Email, Office number, Website Address, Business Address,.
Colors
Designer to choose colors to be used in the design.
Requirements
Must have
- A luxury designer feel. Must be black or dark grey but open to other luxury ideas.
Nice to have
- Gold, silver, black embossing or debossing. Textured paper design.
Should not have
- A cheap look and feel.

```html
<!DOCTYPE html>
<html lang="en">
<head>
<meta charset="utf-8">
<title>528BUILDA Business Card</title>
<link rel="stylesheet" href="https://fonts.googleapis.com/css2?family=Roboto:wght@400;500;700&display=swap">
<style>
  :root {
    --backdrop: #7c7c7c;
    --card: #0d0d0d;
    --card-edge: #1a1a1a;
    --gold: #c2a043;
    --gold-dark: #a88a33;
    --white: #ffffff;
  }
  * { margin: 0; padding: 0; box-sizing: border-box; }
  html, body {
    width: 1093px; height: 1200px; overflow: hidden;
    background: var(--backdrop);
    font-family: "Roboto", Arial, sans-serif;
  }
  .canvas { position: relative; width: 1093px; height: 1200px; }

  .card {
    position: absolute; left: 265px; width: 580px; height: 358px;
    border-radius: 28px;
    background: linear-gradient(160deg, var(--card-edge) 0%, var(--card) 55%, #141414 100%);
    overflow: hidden;
  }
  .card--front { top: 226px; }
  .card--back { top: 620px; }

  /* Front */
  .brand-name {
    position: absolute; right: 330px; top: 262px;
    font-weight: 500; font-size: 31px; line-height: 1; letter-spacing: 1px;
    color: var(--gold); white-space: nowrap;
  }
  .divider {
    position: absolute; left: 289px; top: 93px; width: 1px; height: 170px;
    background: var(--gold-dark);
  }
  .contact { position: absolute; left: 311px; top: 90px; color: var(--gold); }
  .contact__name { font-weight: 700; font-size: 24px; line-height: 24px; letter-spacing: 0.2px; }
  .contact__role { font-size: 17px; line-height: 20px; margin-top: -2px; }
  .contact__list { list-style: none; margin-top: 14px; }
  .contact__item {
    display: flex; align-items: center; gap: 6px;
    font-size: 17px; line-height: 21px;
  }
  .contact__item svg { width: 15px; height: 15px; flex: none; }
  .contact__address { font-size: 17px; line-height: 21px; margin-top: 10px; }

  /* Back */
  .back-texture {
    position: absolute; inset: 0;
    background: radial-gradient(ellipse at 50% 55%, #1b1b1b 0%, #111 60%, #0b0b0b 100%);
  }
  .back-brand {
    position: absolute; left: 0; right: 0; top: 192px;
    display: flex; flex-direction: column; align-items: center;
    color: var(--white);
  }
  .back-brand__name {
    font-weight: 500; font-size: 42px; line-height: 1; letter-spacing: 2px;
  }
  .back-brand__tagline {
    font-weight: 500; font-size: 10px; line-height: 1; letter-spacing: 2.6px;
    margin-top: 5px;
  }
</style>
</head>
<body>
<main class="canvas">

  <section class="card card--front" aria-label="Business card front">
    <div class="brand-name">528BUILDA</div>
    <div class="divider"></div>
    <div class="contact">
      <h1 class="contact__name">MARCUS HALE</h1>
      <p class="contact__role">Managing Director</p>
      <ul class="contact__list">
        <li class="contact__item">
          <svg viewBox="0 0 24 24" fill="none" stroke="currentColor" stroke-width="2.2" stroke-linecap="round" stroke-linejoin="round"><path d="M5 3h4l2 5-2.5 1.5a11 11 0 0 0 6 6L16 13l5 2v4a2 2 0 0 1-2 2A16 16 0 0 1 3 5a2 2 0 0 1 2-2z"/></svg>
          <span>044-987 654 321</span>
        </li>
        <li class="contact__item">
          <svg viewBox="0 0 24 24" fill="currentColor"><path d="M2 5h20v14H2z"/><path d="M2 5l10 8 10-8" fill="none" stroke="#0d0d0d" stroke-width="1.6"/></svg>
          <span>hello@528builda.com</span>
        </li>
        <li class="contact__item">
          <svg viewBox="0 0 24 24" fill="none" stroke="currentColor" stroke-width="1.8"><circle cx="12" cy="12" r="9.5"/><ellipse cx="12" cy="12" rx="4" ry="9.5"/><path d="M2.5 12h19M4 7h16M4 17h16"/></svg>
          <span>www.528builda.com</span>
        </li>
      </ul>
      <p class="contact__address">421, Address line goes here<br>45452,Country Name</p>
    </div>
  </section>

  <section class="card card--back" aria-label="Business card back">
    <div class="back-texture" role="img" aria-label="Dark tonal grid texture of glossy squares"></div>
    <div class="back-brand">
      <div class="back-brand__name">528BUILDA</div>
      <div class="back-brand__tagline">Design and Renovation Firm</div>
    </div>
  </section>

</main>
</body>
</html>
```